Professional & attention grabbing.

A business card design, front and back. I already have a logo I will attach, but I am open to something new as well.
Things to include:
Name:
Title:
Phone:
Email:
Wanting something that is professional but attention grabbing.
Also we do a lot of work using drones on natural gas pipelines (leading the future)if you want to include any of that. I'm open to ideas.
Target Market(s)
Natural gas transmission industry / greenhouse gas mitigation industry
Industry/Entity Type
Business
Colors
Designer to choose colors to be used in the design.
Look and feel
Each slider illustrates characteristics of the customer's brand and the style your logo design should communicate.

```html
<!DOCTYPE html>
<html lang="en">
<head>
<meta charset="utf-8">
<title>Ostrel Inspections – Business Card</title>
<link rel="stylesheet" href="https://fonts.googleapis.com/css2?family=Saira:wght@400;500;600;700&display=swap">
<style>
  :root {
    --backdrop: #858585;
    --card: #fcfcfc;
    --brand-red: #c41e24;
    --ink: #37373a;
    --ink-soft: #3f3f42;
  }
  * { margin: 0; padding: 0; box-sizing: border-box; }
  html, body { width: 1200px; height: 900px; overflow: hidden; }
  body {
    background: var(--backdrop);
    font-family: "Saira", "Helvetica Neue", Arial, sans-serif;
    position: relative;
  }
  .card {
    position: absolute;
    top: 271px;
    width: 458px;
    height: 282px;
    background: var(--card);
    border-radius: 12px;
    overflow: hidden;
  }
  .card--front { left: 137px; }
  .card--back { left: 626px; }

  .brand {
    position: absolute;
    display: flex;
    align-items: center;
    gap: 10px;
    color: var(--ink);
    font-weight: 600;
    line-height: 1;
    white-space: nowrap;
  }
  .brand__mark { background: var(--brand-red); flex: none; }
  .card--front .brand { left: 28px; top: 48px; font-size: 26px; }
  .card--front .brand__mark { width: 22px; height: 22px; }
  .card--back .brand { left: 50%; top: 122px; transform: translateX(-50%); font-size: 34px; }
  .card--back .brand__mark { width: 28px; height: 28px; }

  .person { position: absolute; left: 28px; top: 161px; }
  .person__name {
    color: var(--brand-red);
    font-size: 19px;
    font-weight: 700;
    letter-spacing: 0.5px;
    line-height: 1.1;
  }
  .person__title {
    color: var(--ink);
    font-size: 14px;
    font-weight: 400;
    letter-spacing: 0.6px;
    line-height: 1.35;
  }

  .contact {
    position: absolute;
    left: 28px;
    top: 218px;
    list-style: none;
    color: var(--ink);
    font-size: 13.5px;
  }
  .contact li { display: flex; align-items: center; gap: 8px; height: 21px; }
  .contact svg { width: 11px; height: 11px; flex: none; }

  .address {
    position: absolute;
    right: 29px;
    top: 223px;
    text-align: right;
    color: var(--ink);
    font-size: 13.5px;
    font-style: normal;
    line-height: 17px;
  }

  .footer-bar { position: absolute; bottom: 0; height: 13px; }
  .footer-bar--red { left: 0; width: 225px; background: var(--brand-red); }
  .footer-bar--dark { left: 232px; right: 0; background: var(--ink-soft); }

  .edge-band { position: absolute; left: 0; right: 0; height: 12px; background: var(--brand-red); }
  .edge-band--top { top: 0; }
  .edge-band--bottom { bottom: 0; height: 13px; }
</style>
</head>
<body>

  <section class="card card--front" aria-label="Card front">
    <div class="brand"><span class="brand__mark"></span>Ostrel Inspections</div>

    <div class="person">
      <p class="person__name">DANIEL MOREAU</p>
      <p class="person__title">DIRECTOR</p>
    </div>

    <ul class="contact">
      <li>
        <svg viewBox="0 0 11 11" aria-hidden="true">
          <rect width="11" height="11" fill="#c41e24"/>
          <path d="M3 3.2c.4-.5.9-.5 1.1 0l.4.8c.1.3 0 .5-.2.7l-.3.3c.4.8 1 1.4 1.8 1.8l.3-.3c.2-.2.4-.3.7-.2l.8.4c.5.2.5.7 0 1.1-.6.6-1.6.5-2.6-.1-1-.6-1.8-1.4-2.3-2.4-.4-.9-.3-1.6.3-2.1z" fill="#fff"/>
        </svg>
        418-207-6620
      </li>
      <li>
        <svg viewBox="0 0 11 11" aria-hidden="true">
          <rect width="11" height="11" fill="#c41e24"/>
          <rect x="2.5" y="3.5" width="6" height="4" fill="none" stroke="#fff" stroke-width="1"/>
          <path d="M2.5 3.5l3 2.2 3-2.2" fill="none" stroke="#fff" stroke-width="0.9"/>
        </svg>
        hello@ostrelinspect.com
      </li>
    </ul>

    <address class="address">
      1180 Harbourview Lane,<br>
      Westbrook Heights, Osaka
    </address>

    <div class="footer-bar footer-bar--red"></div>
    <div class="footer-bar footer-bar--dark"></div>
  </section>

  <section class="card card--back" aria-label="Card back">
    <div class="edge-band edge-band--top"></div>
    <div class="brand"><span class="brand__mark"></span>Ostrel Inspections</div>
    <div class="edge-band edge-band--bottom"></div>
  </section>

</body>
</html>
```